SnackOrbit!!! A Vending Machine Business Looking for an attractive website.

We are a vending machine business in Northern Michigan. We have changed our name and have rebranded our company. We would like an attractive website that shares who we are, what services we provide, the products we offer in our machines, along with a form businesses can fill out to see if they are a good fit for our company. I would like to have a Home Page, About SnackOrbit, Why Choose SnackOrbit?, Products & Services, Contact Us (With a Login Option), and a page with a questionnaire for thos interested in getting a FREE Vending Machine.

Target Market(s)

Businesses, Campgrounds, Schools, and many more in Northern Michigan

Industry/Entity Type

Vending Machines

Coding

Coded - Design and coding required

Number of Pages Required

5+ page

Requirements
Must have
• An inviting and enticing Home Page. I want to get my potential clients engaged in our website.
Nice to have
• Possibly background photos from Northern Michigan
Should not have
• A corporate feel. I do not want a boring website.

```html
<!DOCTYPE html>
<html lang="en">
<head>
<meta charset="UTF-8">
<title>SnackOrbit – Crave. Vend. Repeat</title>
<link href="https://fonts.googleapis.com/css2?family=Outfit:wght@300;400;500;600&display=swap" rel="stylesheet">
<style>
:root{
  --navy:#28245f;
  --navy-dark:#211d52;
  --green:#3b5a24;
  --ink:#1d1d1d;
  --text:#444;
  --line:#e4e4ea;
  --gold:#f5b400;
  --white:#fff;
}
*{margin:0;padding:0;box-sizing:border-box}
html,body{width:1200px;height:3288px;overflow:hidden}
body{font-family:'Outfit',sans-serif;color:var(--ink);background:var(--white);position:relative}
.abs{position:absolute}
.btn{position:absolute;display:flex;align-items:center;justify-content:center;font-size:13.5px;font-weight:500;border-radius:3px;color:var(--white);background:var(--navy)}

/* header */
.site-header{position:absolute;top:0;left:0;width:1200px;height:86px;background:var(--white)}
.brand{position:absolute;left:142px;top:18px;display:flex;align-items:center;gap:10px;font-size:34px;font-weight:600;color:var(--navy)}
.brand-dot{width:38px;height:38px;border-radius:50%;background:var(--green)}
.main-nav a{position:absolute;top:33px;font-size:14px;color:var(--ink);text-decoration:none}
.main-nav a.active{color:var(--green);font-weight:500}
.login{left:957px;top:25px;width:101px;height:34px;border-radius:4px}

/* hero */
.hero{position:absolute;top:86px;left:0;width:1200px;height:528px}
.hero-photo{position:absolute;inset:0;background:linear-gradient(90deg,#2e2c2b 0%,#4a4643 35%,#8a7f76 55%,#c9bfb3 72%,#3f3d6b 100%)}
.hero-shade{position:absolute;inset:0;background:linear-gradient(90deg,rgba(0,0,0,.45),rgba(0,0,0,.1) 60%,rgba(0,0,0,0))}
.hero h1{position:absolute;left:142px;top:152px;font-size:46px;font-weight:500;line-height:55px;color:var(--white)}
.hero p{position:absolute;left:142px;top:276px;font-size:23px;color:var(--white)}
.hero .btn{left:142px;top:328px;width:101px;height:33px}

/* about */
.about{position:absolute;top:614px;left:0;width:1200px;height:351px;background:var(--navy);color:var(--white);text-align:center}
.about h2{position:absolute;top:78px;width:100%;font-size:32px;font-weight:500}
.about p{position:absolute;left:230px;top:124px;width:740px;font-size:13.5px;line-height:22px;font-weight:300}
.about .btn{left:548px;top:232px;width:102px;height:35px;background:transparent;border:1px solid var(--white)}

/* why */
.why-title{position:absolute;top:1040px;width:1200px;text-align:center;font-size:32px;font-weight:500}
.feature{position:absolute;width:442px;height:232px;border:1px solid var(--line);background:var(--white)}
.feature-icon{position:absolute;left:14px;top:-37px;width:76px;height:76px;border-radius:50%;background:var(--navy);border:3px solid var(--white);box-shadow:0 0 0 1.5px var(--navy);display:flex;align-items:center;justify-content:center}
.feature h3{position:absolute;left:13px;top:55px;font-size:16px;font-weight:500}
.feature p{position:absolute;left:14px;top:82px;width:410px;font-size:13.5px;line-height:22px;font-weight:300;color:var(--text)}
.feature p b{font-weight:500;color:var(--ink)}

/* cta */
.cta{position:absolute;top:1785px;left:0;width:1200px;height:526px}
.cta-photo{position:absolute;inset:0;background:linear-gradient(90deg,#5f717c 0%,#4a5b66 20%,#b3322a 35%,#4e6069 45%,#5d6e78 60%,#5b6c76 100%)}
.cta h2{position:absolute;left:677px;top:152px;font-size:32px;font-weight:500;line-height:39px;color:var(--white)}
.cta p{position:absolute;left:677px;top:248px;width:385px;font-size:13.5px;line-height:22px;font-weight:300;color:var(--white)}
.cta .btn{left:677px;top:329px;width:102px;height:35px}

/* testimonials */
.testi-title{position:absolute;top:2386px;width:1200px;text-align:center;font-size:32px;font-weight:500}
.review{position:absolute;width:268px;height:282px;border:1px solid var(--line);background:var(--white);text-align:center}
.quote{position:absolute;left:14px;top:-32px;font-size:70px;line-height:70px;font-weight:600;color:var(--navy)}
.avatar{position:absolute;left:111px;top:22px;width:44px;height:44px;border-radius:50%;background:#d7c7b8}
.stars{position:absolute;top:78px;width:100%;display:flex;justify-content:center;gap:5px}
.review p{position:absolute;left:14px;top:114px;width:240px;font-size:13.5px;line-height:23px;font-weight:300;color:var(--text)}
.review .name{position:absolute;top:244px;width:100%;font-size:12.5px;font-weight:500}
.arrow{position:absolute;top:2572px;width:35px;height:35px;border-radius:50%;background:var(--white);box-shadow:0 1px 6px rgba(0,0,0,.15);display:flex;align-items:center;justify-content:center}

/* footer */
.site-footer{position:absolute;top:2911px;left:0;width:1200px;height:377px;background:var(--navy);color:var(--white)}
.footer-badge{position:absolute;left:488px;top:2831px;width:224px;height:224px;border-radius:50%;background:var(--white);border:7px solid var(--green);display:flex;align-items:center;justify-content:center;font-size:31px;font-weight:600;color:var(--navy);gap:8px}
.footer-badge span.dot{width:26px;height:26px;border-radius:50%;background:var(--green)}
.rule{position:absolute;left:142px;width:916px;height:1px;background:rgba(255,255,255,.2)}
.footer-nav a{position:absolute;top:186px;font-size:13.5px;color:var(--white);text-decoration:none;font-weight:300}
.footer-nav a.active{font-weight:600}
.contact-item{position:absolute;top:258px;display:flex;align-items:center;gap:14px;font-size:13.5px;font-weight:300}
.contact-icon{width:38px;height:38px;border-radius:50%;background:rgba(255,255,255,.15);display:flex;align-items:center;justify-content:center}
.contact-item b{display:block;font-weight:500;font-size:12px}
.vsep{position:absolute;top:266px;width:1px;height:28px;background:rgba(255,255,255,.2)}
.copyright{position:absolute;left:142px;top:350px;font-size:13px;font-weight:300}
.socials{position:absolute;left:925px;top:343px;display:flex;gap:5px}
.socials span{width:30px;height:30px;border-radius:50%;border:1.5px solid var(--white)}
</style>
</head>
<body>

<header class="site-header">
  <div class="brand"><span class="brand-dot"></span>SnackOrbit</div>
  <nav class="main-nav">
    <a class="active" style="left:453px">Home</a>
    <a style="left:518px">About</a>
    <a style="left:583px">Why Choose Us</a>
    <a style="left:710px">Products &amp; Services</a>
    <a style="left:860px">Contact Us</a>
  </nav>
  <a class="btn login">Log In</a>
</header>

<section class="hero">
  <div class="hero-photo" role="img" aria-label="Two stocked snack vending machines in a modern office break area"></div>
  <div class="hero-shade"></div>
  <h1>SnackOrbit :<br>Crave. Vend. Repeat</h1>
  <p>Elevating Snacking, One Vend at a Time</p>
  <a class="btn">Contact Us</a>
</section>

<section class="about">
  <h2>About SnackOrbit</h2>
  <p>Welcome to SnackOrbit, where snacking meets delight! We're not just about vending machines;we're your culinary companions, your flavor curators, and your secret stash of happiness. Mara and Owen, the dynamic duo behind SnackOrbit, have a passion for all things tasty. With backgrounds in sales and a penchant for personal connections, they've transformed the vending experience into an art form.</p>
  <a class="btn">Read More</a>
</section>

<h2 class="why-title">Why Choose SnackOrbit?</h2>

<article class="feature" style="left:140px;top:1163px">
  <div class="feature-icon"><svg width="40" height="40" viewBox="0 0 40 40" fill="none" stroke="#fff" stroke-width="2"><path d="M20 32 C8 23 6 17 9 12 c3-4 8-4 11 1 c3-5 8-5 11-1 c3 5 1 11-11 20z"/></svg></div>
  <h3>Local Love</h3>
  <p>We celebrate the heart of Michigan by partnering with local legends. Say hello to <b>Pine Ridge Jerky and North Shore Kettle Chips</b>—our hometown heroes. Their flavors dance on your taste buds, and we're thrilled to bring them straight to your workplace.</p>
</article>

<article class="feature" style="left:618px;top:1163px">
  <div class="feature-icon"><svg width="40" height="40" viewBox="0 0 40 40" fill="none" stroke="#fff" stroke-width="2"><circle cx="20" cy="20" r="13"/><circle cx="15" cy="17" r="1.5" fill="#fff"/><circle cx="25" cy="17" r="1.5" fill="#fff"/><path d="M14 24 q6 6 12 0"/></svg></div>
  <h3>Unleash Your Cravings</h3>
  <p>SnackOrbit isn't bound by corporate ties. We're the rebels of the vending world. Craving a bag of crispy, kettle-cooked chips? Done. Hankering for jerky that packs a punch? We've got you covered. Our machines are like treasure chests, waiting for you to unlock flavor magic.</p>
</article>

<article class="feature" style="left:140px;top:1467px">
  <div class="feature-icon"><svg width="40" height="40" viewBox="0 0 40 40" fill="none" stroke="#fff" stroke-width="2"><circle cx="20" cy="20" r="13"/><path d="M13 20 l5 5 l9-10"/></svg></div>
  <h3>Quality Meets Convenience</h3>
  <p>Imagine this: You're mid-meeting, and your stomach growls. Fear not! SnackOrbit's machines offer top-notch snacks and beverages. It's like having a mini food festival at your fingertips. <b>Tap to Pay</b> : No fumbling for change! SnackOrbit accepts tap-to-pay options, credit cards, and even phone wallet pay. Seamless snacking, guaranteed.</p>
</article>

<article class="feature" style="left:618px;top:1467px">
  <div class="feature-icon"><svg width="40" height="40" viewBox="0 0 40 40" fill="none" stroke="#fff" stroke-width="2"><path d="M8 32 h24"/><rect x="11" y="22" width="4" height="10"/><rect x="18" y="17" width="4" height="15"/><rect x="25" y="12" width="4" height="20"/><path d="M9 18 l8-7 l5 4 l9-8"/></svg></div>
  <h3>Pandemic-Proof &amp; Recession-Ready</h3>
  <p>Life throws curveballs, but SnackOrbit stands strong. Our vending machines are the unsung heroes of resilience. Rain or shine, they're there, serving up joy.</p>
</article>

<section class="cta">
  <div class="cta-photo" role="img" aria-label="A snack vending machine and a red cold drinks machine against a grey wall"></div>
  <h2>Ready to experience the<br>SnackOrbit difference?</h2>
  <p>Sign up now and let's connect. Taste the future of snacking firsthand! Contact us today and explore how our vending magic can elevate your space.</p>
  <a class="btn">Contact Us</a>
</section>

<h2 class="testi-title">Customer Testimonials</h2>

<div class="arrow" style="left:90px"><svg width="14" height="10" viewBox="0 0 14 10" fill="none" stroke="#999" stroke-width="1.2"><path d="M13 5H1M5 1L1 5l4 4"/></svg></div>
<div class="arrow" style="left:1074px"><svg width="14" height="10" viewBox="0 0 14 10" fill="none" stroke="#222" stroke-width="1.2"><path d="M1 5h12M9 1l4 4-4 4"/></svg></div>

<article class="review" style="left:140px;top:2489px">
  <span class="quote">“</span>
  <div class="avatar" role="img" aria-label="Customer portrait"></div>
  <div class="stars"><svg width="78" height="12" viewBox="0 0 78 12" fill="#f5b400"><g id="s"><path d="M6 0l1.8 3.9 4.2.4-3.2 2.8 1 4.1L6 9.1 2.2 11.2l1-4.1L0 4.3l4.2-.4z"/></g><use href="#s" x="16.5"/><use href="#s" x="33"/><use href="#s" x="49.5"/><use href="#s" x="66"/></svg></div>
  <p>Lorem ipsum dolor sit amet, consectetur adipiscing elit, sed do eiusmod tempor incididunt ut labore et dolore magna aliqua.</p>
  <div class="name">-Rob Kessler</div>
</article>

<article class="review" style="left:466px;top:2454px">
  <span class="quote">“</span>
  <div class="avatar" role="img" aria-label="Customer portrait" style="background:#c9a58a"></div>
  <div class="stars"><svg width="78" height="12" viewBox="0 0 78 12" fill="#f5b400"><use href="#s"/><use href="#s" x="16.5"/><use href="#s" x="33"/><use href="#s" x="49.5"/><use href="#s" x="66"/></svg></div>
  <p>Lorem ipsum dolor sit amet, consectetur adipiscing elit, sed do eiusmod tempor incididunt ut labore et dolore magna aliqua.</p>
  <div class="name">-Dana Whitfield</div>
</article>

<article class="review" style="left:791px;top:2489px">
  <span class="quote">“</span>
  <div class="avatar" role="img" aria-label="Customer portrait" style="background:#d9c3b5"></div>
  <div class="stars"><svg width="78" height="12" viewBox="0 0 78 12" fill="#f5b400"><use href="#s"/><use href="#s" x="16.5"/><use href="#s" x="33"/><use href="#s" x="49.5"/><use href="#s" x="66"/></svg></div>
  <p>Lorem ipsum dolor sit amet, consectetur adipiscing elit, sed do eiusmod tempor incididunt ut labore et dolore magna aliqua.</p>
  <div class="name">-Evan Marsh</div>
</article>

<footer class="site-footer">
  <div class="rule" style="top:168px"></div>
  <nav class="footer-nav">
    <a class="active" style="left:226px">Home</a>
    <a style="left:359px">About</a>
    <a style="left:491px">Why Choose Us</a>
    <a style="left:684px">Products &amp; Services</a>
    <a style="left:902px">Contact Us</a>
  </nav>
  <div class="rule" style="top:224px"></div>

  <div class="contact-item" style="left:202px">
    <span class="contact-icon"><svg width="16" height="12" viewBox="0 0 16 12" fill="none" stroke="#fff" stroke-width="1.3"><rect x=".7" y=".7" width="14.6" height="10.6" rx="1"/><path d="M1 1l7 6 7-6"/></svg></span>
    <div><b>Email</b>info@snackorbit.com</div>
  </div>
  <div class="vsep" style="left:422px"></div>
  <div class="contact-item" style="left:492px">
    <span class="contact-icon"><svg width="12" height="16" viewBox="0 0 12 16" fill="#fff"><path d="M6 0a6 6 0 0 0-6 6c0 4.5 6 10 6 10s6-5.5 6-10a6 6 0 0 0-6-6zm0 8.3A2.3 2.3 0 1 1 6 3.7a2.3 2.3 0 0 1 0 4.6z"/></svg></span>
    <div style="line-height:17px">123, Building Name,<br>Street City, State XY 1234</div>
  </div>
  <div class="vsep" style="left:781px"></div>
  <div class="contact-item" style="left:851px">
    <span class="contact-icon"><svg width="16" height="16" viewBox="0 0 16 16" fill="#fff"><path d="M3.6 1l2.2 3-1.3 1.6a9 9 0 0 0 5.9 5.9L12 10.2l3 2.2-1.2 2.6C7.5 15 1 8.5 1 2.2z"/></svg></span>
    <div><b>Phone</b><span style="font-size:16px">123-456-7890</span></div>
  </div>

  <div class="rule" style="top:338px"></div>
  <div class="copyright">© 2024 Snackorbit. All Rights Reserved.</div>
  <div class="socials"><span></span><span></span><span></span><span></span></div>
</footer>

<div class="footer-badge"><span class="dot"></span>SnackOrbit</div>

</body>
</html>
```